KRV Boltmaster Manufacturer New Web Design

We need a new theme designed for metal fastener manufacturing company, KRV Boltmaster Group, a $60M division of Marrowfield Forge Holdings, Inc. We manufacture screw, pins and washers to industrial customers (non-Automotive) such as HN Homeware, Paul Brenner, LUX, Venmora, etc. Our current website is www.boltmaster.example. We would like to stick with the same logo/color scheme, however, I'm aiming to modernize the website's look and feel.

Here are some of our competitor's websites:
- https://www.torvalink.example/
- http://glenrivet.example/
- http://www.harlowbuiltjoining.example/
- http://lugsandcustoms.example/
- http://www.dunmerebolt.example/

Target Market(s)

We primarily want to target engineers working in the following markets:
- Appliance (HN Homeware, Frostavel)
- Ag (Brenner, LUX)
- Recreational Vehicle (Venmora, Tundra Fox)
- Outdoor Power (Brellvik, Pask)

We secondarily want to target buyers working at the above markets as well as buyers at Fastener distributors such as Boltique, Parts Dynamics, Kessel Fordham.

Industry/Entity Type

Metal Forging

Number of Pages Required

1 page

Requirements
Must have
• For products: "Threaded" product as the primary focus. "Pins" product is the secondary focus, followed by all others.
• Please use same logo and color scheme as I do not plan to change.
Nice to have
• Highlight our featured proprietary products (pamphlets attached). KRV Boltmaster's GRIP-N, KelDrive, Boltmaster Coil, Avalanche.

```html
<!DOCTYPE html>
<html lang="en">
<head>
<meta charset="utf-8">
<title>KRV Boltmaster Group</title>
<link rel="stylesheet" href="https://fonts.googleapis.com/css2?family=Roboto+Condensed:wght@400;700&family=Open+Sans:wght@400;600&display=swap">
<style>
:root{
  --green:#1b9a72;
  --blue:#1d7fd2;
  --blue-deep:#1765b8;
  --ink:#111;
  --muted:#8a8a8a;
  --band:#e6e6e6;
  --white:#fff;
  --footer:#000;
  --footer-base:#1b1b1b;
  --head:"Roboto Condensed",Arial Narrow,sans-serif;
  --body:"Open Sans",Arial,sans-serif;
}
*{box-sizing:border-box;margin:0;padding:0}
html,body{width:1200px;height:2394px;overflow:hidden}
body{position:relative;background:var(--white);font-family:var(--body);color:var(--ink)}
a{color:inherit;text-decoration:none}

/* header */
.site-header{position:absolute;left:0;top:0;width:1200px;height:116px;background:var(--white)}
.contact-strip{position:absolute;left:675px;top:0;width:425px;height:35px;background:var(--green);
  clip-path:polygon(28px 0,100% 0,100% 100%,0 100%);display:flex;align-items:center;gap:28px;padding-left:42px;color:var(--white);font-size:13px}
.contact-strip span{display:flex;align-items:center;gap:7px;white-space:nowrap}
.brand{position:absolute;left:118px;top:27px;display:flex;align-items:center;gap:10px}
.brand-dot{width:60px;height:60px;border-radius:50%;background:var(--blue)}
.brand-name{font-family:var(--body);font-weight:600;font-size:21px;color:var(--blue);white-space:nowrap}
.main-nav{position:absolute;left:459px;top:67px;display:flex;gap:27px;font-family:var(--head);font-weight:700;font-size:14.5px;white-space:nowrap}
.main-nav .active{color:var(--blue)}

/* hero */
.hero{position:absolute;left:0;top:116px;width:1200px;height:471px;background:linear-gradient(180deg,#fafafa,#eeeeee)}
.hero-photo{position:absolute;left:463px;top:12px;width:737px;height:459px;background:linear-gradient(160deg,#dfe4ea,#aab3bd 60%,#c8ced5)}
.hero-title{position:absolute;left:118px;top:148px;font-family:var(--head);font-weight:700;font-size:37px;line-height:43px;color:var(--ink)}
.hero-title em{font-style:normal;color:var(--blue)}
.hero-text{position:absolute;left:118px;top:237px;width:400px;font-size:15px;line-height:24px;color:#a8a8a8}
.slide-arrow{position:absolute;top:180px;width:50px;height:50px;border:2px solid #333;border-radius:50%;background:rgba(255,255,255,.7);display:flex;align-items:center;justify-content:center}

/* products */
.products{position:absolute;left:0;top:587px;width:1200px;height:347px;background:var(--band)}
.product-card{position:absolute;top:24px;width:230px;height:262px;background:var(--white);box-shadow:0 2px 8px rgba(0,0,0,.15);text-align:center}
.product-photo{position:absolute;left:30px;top:-56px;width:170px;height:170px;border-radius:50%;border:5px solid var(--white);box-shadow:0 1px 5px rgba(0,0,0,.25)}
.product-card h3{position:absolute;top:125px;width:100%;font-family:var(--head);font-weight:700;font-size:20px}
.product-card p{position:absolute;top:151px;left:25px;width:180px;font-size:11.5px;line-height:19px;color:#777}
.btn-green{display:inline-block;background:var(--green);color:var(--white);font-family:var(--head);font-weight:700;font-size:14px;text-align:center}
.product-card .btn-green{position:absolute;left:56px;top:200px;width:118px;height:30px;line-height:30px}

/* about */
.about{position:absolute;left:0;top:937px;width:1200px;height:423px;background:linear-gradient(135deg,#1f74cc,#1560b0);color:var(--white);text-align:center}
.about-mark{position:absolute;left:565px;top:902px;width:70px;height:70px;border-radius:50%;background:var(--white);box-shadow:0 1px 5px rgba(0,0,0,.25);display:flex;align-items:center;justify-content:center;z-index:2}
.about-mark i{width:52px;height:52px;border-radius:50%;background:var(--blue)}
.about h2{position:absolute;top:88px;width:100%;font-family:var(--head);font-weight:400;font-size:33px;letter-spacing:.5px}
.about p{position:absolute;left:195px;top:141px;width:810px;font-size:16.5px;line-height:27px}
.btn-outline{position:absolute;left:528px;top:268px;width:141px;height:40px;border:2px solid var(--white);line-height:36px;font-family:var(--head);font-weight:700;font-size:15px}

/* features */
.feature{position:absolute;top:1309px;width:468px;height:284px;border:1px solid #ccc;overflow:hidden}
.feature-quality{left:107px;background:linear-gradient(90deg,#f2f2f2,#dcdcdc)}
.feature-eng{left:608px;background:#1e2226}
.feature-photo{position:absolute;top:0;height:100%}
.feature h2{position:absolute;left:44px;top:42px;font-family:var(--head);font-weight:400;font-size:28px}
.feature p{position:absolute;left:44px;top:90px;width:200px;font-size:13.5px;line-height:23px}
.feature .btn{position:absolute;left:44px;top:197px;width:128px;height:36px;line-height:36px}
.feature-eng h2,.feature-eng p{color:var(--white)}
.btn-blue{display:inline-block;background:var(--blue);color:var(--white);font-family:var(--head);font-weight:700;font-size:14px;text-align:center}

/* news */
.news{position:absolute;left:0;top:1631px;width:1200px;height:401px;background:var(--band)}
.news h2{position:absolute;left:105px;top:58px;font-family:var(--head);font-weight:400;font-size:28px}
.news-video{position:absolute;left:102px;top:109px;width:359px;height:223px;background:linear-gradient(135deg,#3a3a3a,#6e6e6e 50%,#8a3a3a);box-shadow:0 2px 6px rgba(0,0,0,.25)}
.play{position:absolute;left:144px;top:75px}
.news-item{position:absolute;left:492px;width:580px}
.date{position:absolute;left:0;top:0;width:76px;text-align:center;font-family:var(--head)}
.date b{display:block;height:40px;background:#0a0a0a;color:var(--white);font-size:30px;font-weight:400;line-height:40px}
.date span{display:block;height:34px;background:var(--blue);color:var(--white);font-size:19px;font-weight:700;line-height:34px}
.news-item h3{position:absolute;left:94px;top:6px;font-weight:400;font-size:17px;white-space:nowrap}
.news-item p{position:absolute;left:94px;top:32px;width:490px;font-size:14.5px;line-height:24px;color:#777}
.news-item .more{position:absolute;left:96px;font-size:13.5px;color:var(--blue);font-weight:600}

/* footer */
.site-footer{position:absolute;left:0;top:2032px;width:1200px;height:292px;background:var(--footer);color:var(--white)}
.footer-col{position:absolute;top:58px}
.footer-col h4{font-family:var(--head);font-weight:700;font-size:20px;margin-bottom:17px}
.footer-col li{list-style:none;font-size:14px;line-height:32px;color:#ddd}
.footer-rule{position:absolute;top:55px;width:1px;height:178px;background:#444}
.social{display:flex;gap:6px;margin-top:4px}
.social i{width:38px;height:38px;border:2px solid var(--white);border-radius:50%}
.footer-brand{position:absolute;left:800px;top:180px;display:flex;align-items:center;gap:10px}
.footer-brand i{width:54px;height:54px;border-radius:50%;background:var(--blue)}
.footer-brand span{font-weight:600;font-size:22px;color:var(--blue);white-space:nowrap}
.footer-base{position:absolute;left:0;top:2324px;width:1200px;height:70px;background:var(--footer-base);color:#999;font-size:14px;text-align:center;line-height:58px}
</style>
</head>
<body>

<header class="site-header">
  <div class="contact-strip">
    <span><svg width="16" height="12" viewBox="0 0 16 12"><rect x="0.5" y="0.5" width="15" height="11" fill="#fff"/><path d="M1 1l7 6 7-6" fill="none" stroke="#1b9a72" stroke-width="1.5"/></svg>info@boltmaster.example</span>
    <span><svg width="14" height="14" viewBox="0 0 24 24"><path d="M6.6 10.8a15 15 0 006.6 6.6l2.2-2.2c.3-.3.7-.4 1-.2 1.1.4 2.3.6 3.6.6.6 0 1 .4 1 1V20c0 .6-.4 1-1 1A17 17 0 013 4c0-.6.4-1 1-1h3.5c.6 0 1 .4 1 1 0 1.3.2 2.5.6 3.6.1.3 0 .7-.2 1z" fill="#fff"/></svg>(684) 555 0142</span>
    <svg width="28" height="28" viewBox="0 0 28 28"><circle cx="14" cy="14" r="12.5" fill="none" stroke="#fff" stroke-width="1.5"/><circle cx="12.5" cy="12.5" r="4.5" fill="none" stroke="#fff" stroke-width="1.8"/><path d="M16 16l4 4" stroke="#fff" stroke-width="2"/></svg>
  </div>
  <div class="brand"><i class="brand-dot"></i><span class="brand-name">KRV Boltmaster Group</span></div>
  <nav class="main-nav">
    <a class="active">HOME</a><a>PRODUCTS</a><a>CAPABILITES</a><a>ENGINEERING</a><a>QUALITY</a><a>ABOUT US</a><a>CONTACT US</a>
  </nav>
</header>

<section class="hero">
  <div class="hero-photo" role="img" aria-label="Photo of steel bolts, nuts and screws arranged on a grey surface"></div>
  <h1 class="hero-title">BETTER FASTENERS FOR<br><em>BETTER PRODUCTS</em></h1>
  <p class="hero-text">Curabitur vel mi sit amet magna malesuada ultrices Ut nisi erat fermentum vel congue id euismod</p>
  <div class="slide-arrow" style="left:34px"><svg width="14" height="18" viewBox="0 0 14 18"><path d="M10 2L3 9l7 7" fill="none" stroke="#222" stroke-width="2.5"/></svg></div>
  <div class="slide-arrow" style="left:1105px"><svg width="14" height="18" viewBox="0 0 14 18"><path d="M4 2l7 7-7 7" fill="none" stroke="#222" stroke-width="2.5"/></svg></div>
</section>

<section class="products">
  <article class="product-card" style="left:126px">
    <div class="product-photo" role="img" aria-label="Photo of threaded screws and bolts" style="background:radial-gradient(circle,#a89a80,#4a4238)"></div>
    <h3>THREADED</h3><p>Curabitur vel mi sit amet magna malesuada ultrices Ut nisi</p><a class="btn-green">VIEW ALL</a>
  </article>
  <article class="product-card" style="left:370px">
    <div class="product-photo" role="img" aria-label="Photo of metal pins and clips" style="background:radial-gradient(circle,#d8d3c4,#8c8674)"></div>
    <h3>PINS</h3><p>Curabitur vel mi sit amet magna malesuada ultrices Ut nisi</p><a class="btn-green">VIEW ALL</a>
  </article>
  <article class="product-card" style="left:614px">
    <div class="product-photo" role="img" aria-label="Photo of black and zinc lock washers" style="background:radial-gradient(circle,#8a8a8a,#3c3c3c)"></div>
    <h3>LOCK WASHERS</h3><p>Curabitur vel mi sit amet magna malesuada ultrices Ut nisi</p><a class="btn-green">VIEW ALL</a>
  </article>
  <article class="product-card" style="left:859px">
    <div class="product-photo" role="img" aria-label="Photo of stamped metal washers and clips" style="background:radial-gradient(circle,#c9c9c9,#6f6f6f)"></div>
    <h3>STAMPINGS</h3><p>Curabitur vel mi sit amet magna malesuada ultrices Ut nisi</p><a class="btn-green">VIEW ALL</a>
  </article>
</section>

<div class="about-mark"><i></i></div>
<section class="about">
  <h2>ABOUT OUR COMPANY</h2>
  <p>Vivamus porttitor purus nisi eleifend libero a tempus libero lectus feugiat felis Morbi diam mauris viverra in gravida Au mattis in ante Morbi eget arcu Morbi porta libero id ullamcorper nonummy nibh ligula pulvinar metus eget consectetuer augue nisi quis lacus Ut ac mi quis lacus mollis aliquamMorbi diam mauris viverra in gravida eu mattis in ante Morbi eget arcu Morbi porta libero id</p>
  <a class="btn-outline">READ MORE</a>
</section>

<article class="feature feature-quality">
  <div class="feature-photo" role="img" aria-label="Photo of a single hex head bolt" style="left:250px;width:200px;background:linear-gradient(90deg,rgba(200,200,200,0),#b9b9b9 50%,rgba(200,200,200,0))"></div>
  <h2>OUR QUALITY</h2>
  <p>Morbi diam mauris viverra in gravida eu mattis in ante Morbi eget arcu Morbi porta libero id ullamcorper nonummy</p>
  <a class="btn btn-green">READ MORE</a>
</article>
<article class="feature feature-eng">
  <div class="feature-photo" role="img" aria-label="Photo of two engineers in blue hard hats inspecting a part" style="left:180px;width:288px;background:linear-gradient(120deg,#2a3440,#5a6470 50%,#7a6a58)"></div>
  <h2>ENGINEERING</h2>
  <p>Morbi diam mauris viverra in gravida eu mattis in ante Morbi eget arcu Morbi porta libero id ullamcorper nonummy</p>
  <a class="btn btn-blue">READ MORE</a>
</article>

<section class="news">
  <h2>NEWS &amp; EVENTS</h2>
  <div class="news-video" role="img" aria-label="Video still of fastener production machinery">
    <svg class="play" width="70" height="70" viewBox="0 0 70 70"><circle cx="35" cy="35" r="33" fill="#fff"/><path d="M28 22l20 13-20 13z" fill="#111"/></svg>
  </div>
  <div class="news-item" style="top:109px">
    <div class="date"><b>02</b><span>DEC</span></div>
    <h3>Morbi diam mauris viverra in gravida</h3>
    <p>mattis in ante Morbi eget arcu Morbi porta libero id ullamcorper</p>
    <a class="more" style="top:62px">READ MORE</a>
  </div>
  <div class="news-item" style="top:235px">
    <div class="date"><b>08</b><span>AUG</span></div>
    <h3>KRV Integrates Leading Midwest Fastener Divisions</h3>
    <p>mattis in ante Morbi eget arcu Morbi porta liberMorbi diam mauris viverra in gravida eu mattis in ante Morbi eget arcu libero id</p>
    <a class="more" style="top:84px">READ MORE</a>
  </div>
</section>

<footer class="site-footer">
  <div class="footer-col" style="left:123px"><h4>COMPANY</h4><ul><li>Home</li><li>About Us</li><li>Products</li><li>Contact Us</li></ul></div>
  <div class="footer-rule" style="left:270px"></div>
  <div class="footer-col" style="left:321px"><h4>RESOURCES</h4><ul><li>News &amp; Events</li><li>Capabilities</li><li>Engineering</li><li>Quality</li></ul></div>
  <div class="footer-rule" style="left:484px"></div>
  <div class="footer-col" style="left:559px"><h4>PRODUCTS</h4><ul><li>Threaded</li><li>Pins</li><li>Lock Washers</li><li>Stampings</li></ul></div>
  <div class="footer-rule" style="left:713px"></div>
  <div class="footer-col" style="left:800px"><h4>FOLLOW US</h4><div class="social"><i></i><i></i><i></i><i></i></div></div>
  <div class="footer-brand"><i></i><span>KRV Boltmaster Group</span></div>
</footer>
<div class="footer-base">© 2017 Company Name  All right reserved</div>

</body>
</html>
```